Print materials for 3-star hotel

We are changing up our print materials (notepads, letterheads, key card jackets, small flyer for the room rates) We are a 3 star business hotel in the Philippines and have mainly used grey tones and clean, simple lines. See attached photos for logo and hotel interior photos.

Target Market(s)

Business

Contact Information for Business Card

Corvale Terrace Hotel
Lindwell Banca Avenue corner Tolenta St Cebu City 6000 Philippines
Tel: +63 32 481 7302
Mobile: +63 917 648 2095
www.corvaleterracehotel.example

Font styles to use
Serif
Sans Serif

Requirements
Must have
• Simple
• Readable font and font size
Nice to have
• Neutral colors, grey and taupes
Should not have
• No purples and bright blues

```html
<!DOCTYPE html>
<html lang="en">
<head>
<meta charset="utf-8">
<title>Corvale Terrace Hotel – Business Card</title>
<link rel="stylesheet" href="https://fonts.googleapis.com/css2?family=Crimson+Pro:wght@400;500&display=swap">
<style>
  :root {
    --backdrop: #eceeee;
    --card-stock: #aba8aa;
    --ink: #2e2d2f;
    --ink-soft: #4a484b;
    --rule: #6d6a6d;
    --edge-shadow: rgba(40, 38, 42, 0.22);
  }
  * { box-sizing: border-box; margin: 0; padding: 0; }
  html, body {
    width: 1200px;
    height: 900px;
    overflow: hidden;
    background: var(--backdrop);
  }
  .sheet {
    width: 1200px;
    height: 900px;
    display: flex;
    align-items: center;
    justify-content: center;
    gap: 60px;
  }
  .card {
    position: relative;
    width: 525px;
    height: 300px;
    background: var(--card-stock);
    box-shadow: 0 6px 14px var(--edge-shadow);
    color: var(--ink);
    font-family: "Crimson Pro", serif;
  }

  /* Front */
  .card--front {
    display: flex;
    align-items: center;
    justify-content: center;
  }
  .brand {
    display: flex;
    align-items: center;
    gap: 16px;
  }
  .brand__mark {
    width: 30px;
    height: 30px;
    background: var(--ink);
  }
  .brand__name {
    font-size: 23px;
    font-weight: 400;
    letter-spacing: 0.32em;
    text-transform: uppercase;
    color: var(--ink);
  }

  /* Back */
  .card__mark {
    position: absolute;
    top: 36px;
    right: 44px;
    width: 34px;
    height: 34px;
    background: var(--ink);
  }
  .contact {
    position: absolute;
    left: 40px;
    right: 44px;
    bottom: 40px;
  }
  .contact__name {
    font-size: 22px;
    font-weight: 500;
    letter-spacing: 0.04em;
    text-transform: uppercase;
    line-height: 1.05;
  }
  .contact__title {
    font-size: 14px;
    color: var(--ink-soft);
    line-height: 1.2;
  }
  .contact__rule {
    height: 1px;
    background: var(--rule);
    margin: 9px 0 8px;
  }
  .contact__line {
    font-size: 13.5px;
    color: var(--ink-soft);
    line-height: 1.4;
  }
  .contact__sep { padding: 0 4px; }
</style>
</head>
<body>
  <main class="sheet">
    <section class="card card--front" aria-label="Business card front">
      <div class="brand">
        <span class="brand__mark"></span>
        <span class="brand__name">Corvale Terrace Hotel</span>
      </div>
    </section>

    <section class="card card--back" aria-label="Business card back">
      <span class="card__mark"></span>
      <div class="contact">
        <p class="contact__name">Daniel Ocampo</p>
        <p class="contact__title">CEO/Founder</p>
        <div class="contact__rule"></div>
        <p class="contact__line">4120 Halden Crescent, Marrow Bay, Oregon 58213</p>
        <p class="contact__line">614 208 7391<span class="contact__sep">|</span>mail@corvale.example<span class="contact__sep">|</span>www.corvale.example</p>
      </div>
    </section>
  </main>
</body>
</html>
```